Looking for a cool & simple business-card-design for digital agency

Hi!

We are a web agency that offers Reputation Management, Vextor & Seo Services and software development. We like cool things, we like innovative styles.

We have uploaded our logo.

Project Deadline Extended Reason: Client does not want any designs with the colorful logo. Please send us submissions ONLY with the blac and white logo. What the client would like to see:1) Back of the card: is a silver logo on a black background2) front of the card with all the data, please use white background and black logo thank you Added Friday, May 8, 2015

Industry/Entity Type

Software

```html
<!DOCTYPE html>
<html lang="de">
<head>
<meta charset="utf-8">
<title>Nordwerk AG – Visitenkarte</title>
<link rel="stylesheet" href="https://fonts.googleapis.com/css2?family=Lato:wght@400;700;900&display=swap">
<style>
  :root {
    --stage: #e9e7e3;
    --card-black: #0b0b0b;
    --card-white: #ffffff;
    --silver: #c9c9c9;
    --silver-dim: #9a9a9a;
    --ink: #111111;
    --ink-soft: #3a3a3a;
    --rule: #8c8c8c;
  }
  * { box-sizing: border-box; margin: 0; padding: 0; }
  html, body { width: 1200px; height: 900px; overflow: hidden; }
  body {
    background: var(--stage);
    font-family: "Lato", sans-serif;
    position: relative;
  }
  .card {
    position: absolute;
    left: 285px;
    width: 630px;
    height: 360px;
    box-shadow: 0 10px 28px rgba(0,0,0,0.25);
    overflow: hidden;
  }
  /* Back */
  .card-back { top: 50px; background: var(--card-black); }
  .card-back .brand { position: absolute; left: 70px; top: 128px; color: var(--silver); }
  .card-back .tagline { color: var(--silver-dim); }
  .brand-row { display: flex; align-items: center; gap: 16px; }
  .brand-mark { width: 34px; height: 34px; background: currentColor; }
  .brand-name { font-weight: 900; font-size: 52px; letter-spacing: 1px; line-height: 1; }
  .tagline {
    font-weight: 400; font-size: 22px; letter-spacing: 9px;
    margin: 8px 0 0 50px; text-transform: uppercase;
  }
  /* Front */
  .card-front { top: 480px; background: var(--card-white); }
  .card-front .band {
    position: absolute; left: 0; right: 0; bottom: 0; height: 62px;
    background: var(--card-black);
  }
  .card-front .brand { position: absolute; left: 34px; top: 96px; color: var(--ink); }
  .card-front .brand-mark { width: 22px; height: 22px; }
  .card-front .brand-name { font-size: 32px; }
  .card-front .tagline { font-size: 14px; letter-spacing: 5.5px; margin: 5px 0 0 38px; color: var(--ink-soft); }
  .divider {
    position: absolute; left: 355px; top: 50px; width: 1px; height: 200px;
    background: linear-gradient(to bottom, transparent, var(--rule) 25%, var(--rule) 75%, transparent);
  }
  .contact { position: absolute; left: 378px; top: 58px; color: var(--ink); }
  .contact-name { font-weight: 700; font-size: 21px; }
  .contact-role { font-size: 16px; margin-bottom: 10px; color: var(--ink-soft); }
  .contact-list { list-style: none; }
  .contact-list li { display: flex; align-items: center; gap: 8px; font-size: 18px; line-height: 26px; }
  .contact-list svg { width: 15px; height: 15px; flex: none; fill: var(--ink); }
</style>
</head>
<body>
  <section class="card card-back" aria-label="Kartenrückseite">
    <div class="brand">
      <div class="brand-row"><span class="brand-mark"></span><span class="brand-name">Nordwerk AG</span></div>
      <p class="tagline">Digitale Strategien</p>
    </div>
  </section>

  <section class="card card-front" aria-label="Kartenvorderseite">
    <div class="brand">
      <div class="brand-row"><span class="brand-mark"></span><span class="brand-name">Nordwerk AG</span></div>
      <p class="tagline">Digitale Strategien</p>
    </div>
    <div class="divider"></div>
    <div class="contact">
      <p class="contact-name">Lena Hartmann</p>
      <p class="contact-role">Director</p>
      <ul class="contact-list">
        <li><svg viewBox="0 0 16 16"><path d="M3 2h3l1.5 3.5-2 1.2a8 8 0 0 0 3.8 3.8l1.2-2L14 10v3a1 1 0 0 1-1 1A11 11 0 0 1 2 3a1 1 0 0 1 1-1z"/></svg>040 555 0182</li>
        <li><svg viewBox="0 0 16 16"><path d="M4.5 1h7a1 1 0 0 1 1 1v12a1 1 0 0 1-1 1h-7a1 1 0 0 1-1-1V2a1 1 0 0 1 1-1zm.5 2v9h6V3zm3 10a.8.8 0 1 0 0 1.6A.8.8 0 0 0 8 13z"/></svg>0171 555 0934</li>
        <li><svg viewBox="0 0 16 16"><path d="M1 3h14v10H1zm1.5 1.3v.4L8 8.6l5.5-3.9v-.4zm0 2.2v5h11v-5L8 10.3z"/></svg>info@nordwerkag.com</li>
        <li><svg viewBox="0 0 16 16"><path d="M8 1a7 7 0 1 0 0 14A7 7 0 0 0 8 1zm5.4 6.2h-2.5a11 11 0 0 0-1-4.4 5.6 5.6 0 0 1 3.5 4.4zM8 2.6c.7.9 1.3 2.6 1.4 4.6H6.6C6.7 5.2 7.3 3.5 8 2.6zM6.1 2.8a11 11 0 0 0-1 4.4H2.6a5.6 5.6 0 0 1 3.5-4.4zM2.6 8.8h2.5a11 11 0 0 0 1 4.4 5.6 5.6 0 0 1-3.5-4.4zM8 13.4c-.7-.9-1.3-2.6-1.4-4.6h2.8c-.1 2-.7 3.7-1.4 4.6zm1.9-.2a11 11 0 0 0 1-4.4h2.5a5.6 5.6 0 0 1-3.5 4.4z"/></svg>www.nordwerkag.com</li>
      </ul>
    </div>
    <div class="band"></div>
  </section>
</body>
</html>
```